WordPress Website Design for Multi-Brand Aviation Group (Unified Branding System)

Project Overview:
We are seeking a professional, modern WordPress website design for an aviation-focused umbrella company that owns and operates multiple subsidiary businesses. The goal is to create a cohesive visual system that clearly communicates that each company operates under the same parent organization, while still allowing each brand to maintain a slightly distinct identity.
This is not just a single website design—we are looking for a scalable design framework that can be applied across multiple aviation-related businesses.
Objectives:
- Establish a consistent, recognizable brand identity across all company websites
Clearly communicate the relationship between the parent company and its subsidiaries
-bCreate a clean, high-end corporate aviation aesthetic
- Ensure all designs are SEO-friendly and optimized for performance
- Allow flexibility for future expansion (additional subsidiaries)
- Target Audience:
- Corporate aviation clients
- Charter customers
- Students wishing to receive flight training
- Aircraft owners and operators
- Turbine aircraft training to meet insurance requirements
- Business professionals and high-net-worth individuals
- Aviation industry partners
Design Direction & Style:
We are looking for a premium, professional aviation feel—think clean, modern, and high-trust. The design should reflect the standards of corporate aviation: precision, safety, and sophistication.
Key style notes:
Minimalist but impactful layout
High-quality aviation photography (jets, interiors, operations, global travel)
Subtle motion/interaction (hover effects, transitions)
Clear typography hierarchy for readability and professionalism
Branding Requirements:
Incorporate the primary colors of the parent company logo across all designs
Website Structure (Core Pages):
Design a system that includes:
Home Page with the following links:
- About / Company Overview
- Aircraft Management
- Aircraft Acquisition
- Charter
- Pilot Services
- Trip Support
- Contact Page
Site should further include:
- Mobile-first responsive design
- Fast-loading, performance-optimized layouts
SEO & Technical Considerations:
- Design should support high-level SEO implementation:
- Clean layout structure that translates well to semantic HTML
- Proper heading hierarchy (H1, H2, H3)
- Space for keyword-rich content without clutter
- Optimized image placement (with alt text capability)
- Fast load times (lightweight design approach)
- Compatibility with WordPress SEO plugins (e.g., Yoast or Rank Math)
WordPress Requirements:
- Design should be easily built using WordPress (preferred builders: Elementor, Gutenberg, or similar)
- Reusable templates for scalability across multiple sites
- Easy for non-developers to update text and images
- Modular components (blocks/sections that can be reused across pages and sites)
- Navigation & UX:
- Simple, intuitive navigation
- Sticky header preferred
Style guide including:
- Colors
- Fonts
- Button styles
- Layout system
- Designs similar to high-end corporate aviation, private jet charter, or luxury service brands are preferred—clean, sharp, and premium without being overly flashy.
What We Want to Avoid:
- Overly busy layouts
- Generic templates with no brand identity
- Outdated or “stock” looking aviation designs
- Poor mobile responsiveness
Additional Notes:
We are building a long-term brand system, not just a one-off website. There is potential for ongoing work as we expand additional subsidiary sites.
We value designers who understand branding consistency across multiple business units and can create a scalable, professional system.
Include the attached main company logo "Vireton Aviation Group" and the "Member PJFO" logo on the main page.

```html
<!DOCTYPE html>
<html lang="en">
<head>
<meta charset="utf-8">
<title>Vireton Aviation Group</title>
<link href="https://fonts.googleapis.com/css2?family=Michroma&family=Montserrat:wght@400;500;600;700&display=swap" rel="stylesheet">
<style>
:root{
  --blue:#0a56b0;
  --ink:#1b1b1b;
  --dark:#1c1c1d;
  --grey:#f3f3f4;
  --muted:#8a8f96;
  --line:#d4d6d9;
  --white:#fff;
}
*{box-sizing:border-box;margin:0;padding:0}
html,body{width:1200px;height:4808px;overflow:hidden}
body{position:relative;font-family:"Montserrat",sans-serif;color:var(--ink);background:var(--white)}
.abs{position:absolute}
.display{font-family:"Michroma",sans-serif;text-transform:uppercase;line-height:1.15;letter-spacing:1px;white-space:nowrap}
.eyebrow{font-family:"Michroma",sans-serif;font-size:12px;letter-spacing:2px;text-transform:uppercase;color:var(--muted)}
.btn{display:inline-flex;align-items:center;justify-content:center;gap:6px;height:46px;padding:0 18px;background:var(--blue);color:#fff;font-family:"Michroma",sans-serif;font-size:11px;letter-spacing:1px;text-transform:uppercase;white-space:nowrap}
.btn.light{background:#fff;color:var(--ink)}
.copy{font-size:15px;line-height:1.5}
.photo{position:absolute}
/* header */
.site-header{position:absolute;top:0;left:0;width:1200px;height:78px;background:#fff;box-shadow:0 1px 0 #e6e6e6}
.brand{position:absolute;display:flex;flex-direction:column;font-family:"Michroma",sans-serif;color:var(--blue);text-transform:uppercase;white-space:nowrap}
.nav{position:absolute;top:31px;right:76px;display:flex;gap:30px;font-size:11px;font-weight:700;text-transform:uppercase;white-space:nowrap}
/* hero */
.hero{position:absolute;top:78px;left:0;width:1200px;height:627px}
/* charter cards */
.card{position:absolute;top:1612px;width:324px;height:302px}
.card span{position:absolute;bottom:22px;left:0;right:0;text-align:center;font-family:"Michroma",sans-serif;font-size:15px;color:#fff;letter-spacing:1px;text-transform:uppercase}
.card::after{content:"";position:absolute;inset:10px;border:1px solid rgba(255,255,255,.35)}
/* services */
.svc{position:absolute;top:3390px;width:478px;height:338px;background:#fff;padding:46px 48px}
.svc h3{font-family:"Michroma",sans-serif;font-size:21px;margin:22px 0 16px;letter-spacing:1px;text-transform:uppercase;white-space:nowrap}
/* footer */
.foot-col h4{font-family:"Michroma",sans-serif;font-size:14px;letter-spacing:1.5px;border-left:3px solid var(--blue);padding-left:10px;margin-bottom:20px;text-transform:uppercase;white-space:nowrap}
.foot-col li{list-style:none;font-size:11px;margin-bottom:12px;padding-left:10px}
</style>
</head>
<body>

<header class="site-header">
  <div class="brand" style="left:66px;top:18px">
    <span style="font-size:27px;line-height:1">Vireton</span>
    <span style="font-size:11px;color:var(--ink);letter-spacing:2px">Aviation Group</span>
  </div>
  <nav class="nav">
    <span>About</span><span>Aircraft Management</span><span>Aircraft Acquisition</span><span>Charter</span><span>Pilot Services</span><span>Trip Support</span><span>Contact</span>
  </nav>
</header>

<section class="hero">
  <div class="photo" role="img" aria-label="Private jet on the apron with airstair deployed at dusk" style="inset:0;background:linear-gradient(90deg,#050607 0%,#17191c 35%,#4a5058 65%,#8c8d8f 85%,#3c3f44 100%)"></div>
  <p class="abs eyebrow" style="left:107px;top:178px;color:#fff;font-size:13px">Vireton Aviation Group</p>
  <h1 class="abs display" style="left:105px;top:206px;color:#fff;font-size:41px">Elevating Aviation<br>Excellence</h1>
  <a class="abs btn" style="left:110px;top:326px;width:195px">Learn More ↗</a>
</section>

<section>
  <p class="abs eyebrow" style="left:118px;top:802px">Who we are</p>
  <h2 class="abs display" style="left:118px;top:824px;font-size:33px;color:var(--blue)">About Vireton<br><span style="color:var(--ink);font-size:27px">Avitation Group</span></h2>
  <p class="abs copy" style="left:118px;top:926px;width:440px">Built on the standards of corporate aviation, Vireton Aviation Group brings together multiple specialized companies under one trusted brand. We provide seamless aviation solutions for aircraft owners, operators, charter clients, and aviation professionals.</p>
  <div class="photo" role="img" aria-label="Business jet with airstair on a reflective tarmac" style="left:116px;top:1090px;width:475px;height:257px;background:linear-gradient(160deg,#d9dde2,#7c8896 60%,#2a3542)"></div>
  <div class="photo" role="img" aria-label="Luxury private jet cabin interior with leather seats" style="left:627px;top:800px;width:474px;height:318px;background:linear-gradient(180deg,#3a2a1f,#8a5a34 50%,#2a1e18)"></div>
  <svg class="abs" style="left:840px;top:933px" width="50" height="50" viewBox="0 0 50 50"><circle cx="25" cy="25" r="24" fill="#fff"/><path d="M20 15 L35 25 L20 35Z" fill="#1b1b1b"/></svg>
  <p class="abs copy" style="left:645px;top:1155px;width:440px">Built on the standards of corporate aviation, Vireton Aviation Group brings together multiple specialized companies under one trusted brand. We provide seamless aviation solutions for aircraft owners, operators, charter clients, and aviation professionals.</p>
  <a class="abs btn" style="left:645px;top:1292px;width:195px">Learn More ↗</a>
</section>

<section class="abs" style="top:1446px;left:0;width:1200px;height:625px;background:var(--grey)"></section>
<p class="abs eyebrow" style="left:0;width:1186px;text-align:center;top:1508px;color:var(--blue)">Experience</p>
<h2 class="abs display" style="left:0;width:1186px;text-align:center;top:1530px;font-size:29px">Our Charter</h2>
<div class="card" role="img" aria-label="Private jet parked at sunset" style="left:105px;background:linear-gradient(180deg,#c49a5a,#6f7a86 55%,#2b2f36)"><span>Charter Title</span></div>
<div class="card" role="img" aria-label="Jet flying above the clouds" style="left:451px;background:linear-gradient(180deg,#e9ecef,#b4bcc4 60%,#8a939c)"><span>Charter Title</span></div>
<div class="card" role="img" aria-label="Jet on runway, front view at dusk" style="left:797px;background:linear-gradient(180deg,#9aa6b3,#5d6a78 60%,#2d333b)"><span>Charter Title</span></div>
<div class="abs" style="left:105px;top:1975px;width:1020px;height:2px;background:var(--line)"></div>
<div class="abs" style="left:105px;top:1974px;width:345px;height:4px;background:#555"></div>

<section class="abs" style="top:2071px;left:0;width:1200px;height:607px;background:var(--dark);overflow:hidden">
  <svg class="abs" style="left:0;top:0" width="680" height="607" viewBox="0 0 680 607" role="img" aria-label="Private jet cabin seat lit by sunlight through windows">
    <defs><linearGradient id="cabin" x1="0" y1="0" x2="1" y2="1"><stop offset="0" stop-color="#4b3524"/><stop offset=".5" stop-color="#b98a54"/><stop offset="1" stop-color="#2a2019"/></linearGradient></defs>
    <polygon points="0,0 680,0 500,607 0,607" fill="url(#cabin)"/>
    <line x1="680" y1="0" x2="530" y2="530" stroke="#0a56b0" stroke-width="5"/>
  </svg>
  <p class="abs eyebrow" style="left:703px;top:155px;color:#fff">What we do</p>
  <h2 class="abs display" style="left:702px;top:180px;color:#fff;font-size:31px">Aircraft<br>Management</h2>
  <p class="abs copy" style="left:706px;top:285px;width:440px;color:#fff">Complete operational oversight for private aircraft owners, including maintenance coordination, crew staffing, compliance, scheduling, and cost control.</p>
  <a class="abs btn" style="left:706px;top:383px;width:195px">Learn More ↗</a>
</section>

<section>
  <p class="abs eyebrow" style="left:124px;top:2818px">Why we are</p>
  <h2 class="abs display" style="left:122px;top:2840px;font-size:30px;color:var(--blue)">Aircraft<br><span style="color:var(--ink)">Acquisition</span></h2>
  <p class="abs copy" style="left:124px;top:2940px;width:430px">Complete operational oversight for private aircraft owners, including maintenance coordination, crew staffing, compliance, scheduling, and cost control.</p>
  <p class="abs copy" style="left:124px;top:3020px;width:430px;font-size:16px">Lorem ipsum dolor sit amet, consectetur adipiscing elit, sed do eiusmod tempor incididunt ut labore et dolore magna aliqua. Quis ipsum suspendisse</p>
  <a class="abs btn" style="left:124px;top:3115px;width:188px">Learn More ↗</a>
  <svg class="abs" style="left:585px;top:2740px" width="580" height="500" viewBox="0 0 580 500" role="img" aria-label="Businessman on the phone stepping down a jet airstair">
    <polygon points="145,3 435,3 578,250 435,497 145,497 2,250" fill="none" stroke="#d7d9dc" stroke-width="2"/>
    <defs><linearGradient id="hx" x1="0" y1="0" x2="1" y2="1"><stop offset="0" stop-color="#1d4f9c"/><stop offset=".55" stop-color="#5f86c2"/><stop offset="1" stop-color="#d8dde4"/></linearGradient></defs>
    <polygon points="160,30 420,30 548,250 420,470 160,470 32,250" fill="url(#hx)"/>
  </svg>
</section>

<section>
  <div class="photo" role="img" aria-label="Faded jet parked on the apron" style="left:0;top:3303px;width:1200px;height:690px;background:linear-gradient(180deg,#e9ebee,#f5f6f7 70%,#fff)"></div>
  <div class="svc" style="left:105px">
    <div role="img" aria-label="Pilot icon" style="width:54px;height:50px;background:linear-gradient(135deg,#9dbbe0,#2a5fa8);border-radius:6px"></div>
    <h3>Pilot Services</h3>
    <p class="copy">Lorem ipsum dolor sit amet, consectetur adipiscing elit, sed do eiusmod tempor incididunt ut labore et dolore magna aliqua Quis ipsum suspendis</p>
    <a class="btn" style="margin-top:26px;width:184px">Learn More ↗</a>
  </div>
  <div class="svc" style="left:607px">
    <div role="img" aria-label="Global travel icon" style="width:54px;height:50px;background:linear-gradient(135deg,#c5c8cc,#4a4e55);border-radius:6px"></div>
    <h3>Trip Support</h3>
    <p class="copy">Lorem ipsum dolor sit amet, consectetur adipiscing elit, sed do eiusmod tempor incididunt ut labore et dolore magna aliqua Quis ipsum suspendis</p>
    <a class="btn" style="margin-top:26px;width:184px">Learn More ↗</a>
  </div>
</section>

<section class="abs" style="left:86px;top:3859px;width:1043px;height:517px">
  <div class="photo" role="img" aria-label="Aerial view of private jets parked on a dark apron" style="inset:0;background:linear-gradient(180deg,#3a3a38,#1f2022 45%,#333537)"></div>
  <p class="abs eyebrow" style="left:0;width:1043px;text-align:center;top:91px;color:#fff;font-size:11px">Get in touch</p>
  <h2 class="abs display" style="left:0;width:1043px;text-align:center;top:112px;color:#fff;font-size:31px">Contact Vireton<br>Aviation Group</h2>
  <p class="abs copy" style="left:270px;width:503px;text-align:center;top:200px;color:#fff">Lorem ipsum dolor sit amet, consectetur adipiscing elit, sed do eiusmod tempor incididunt ut labore et dolore</p>
  <a class="abs btn light" style="left:428px;top:262px;width:187px;height:40px">Get in Touch ↗</a>
</section>

<footer>
  <div class="brand" style="left:118px;top:4472px">
    <span style="font-size:33px;line-height:1">Vireton</span>
    <span style="font-size:14px;color:var(--ink);letter-spacing:3px">Aviation Group</span>
  </div>
  <div class="abs" style="left:120px;top:4576px;display:flex;align-items:center;gap:8px">
    <svg width="38" height="38" viewBox="0 0 38 38"><circle cx="19" cy="19" r="18" fill="#0a56b0"/></svg>
    <div><div style="font-size:9px">Member</div><div style="font-family:Michroma,sans-serif;font-size:22px;line-height:1">PJFO</div></div>
  </div>
  <div class="abs foot-col" style="left:456px;top:4468px"><h4>Navigation</h4><ul><li>About</li><li>Aircraft Management</li><li>Aircraft Acquisition</li><li>Charter</li><li>Pilot Services</li></ul></div>
  <div class="abs foot-col" style="left:676px;top:4468px"><h4>Resources</h4><ul><li>Trip Support</li><li>Contact</li><li>Terms of Use</li><li>Privacy Policy</li><li>Sitemap</li></ul></div>
  <div class="abs foot-col" style="left:890px;top:4468px"><h4>Contact Us</h4>
    <ul>
      <li style="display:flex;gap:10px"><svg width="10" height="13" viewBox="0 0 10 13"><path d="M5 0a5 5 0 0 1 5 5c0 3.5-5 8-5 8S0 8.5 0 5a5 5 0 0 1 5-5z" fill="#1b1b1b"/><circle cx="5" cy="5" r="1.8" fill="#fff"/></svg><span>1420 Harbor Crest Dr.<br>Palm Harbor, FL 34683</span></li>
      <li style="display:flex;gap:10px"><svg width="11" height="11" viewBox="0 0 11 11"><path d="M2 0l2 2.5-1.2 1.3a6 6 0 0 0 4.4 4.4L8.5 7 11 9l-1.5 2C4.5 11 0 6.5 0 1.5z" fill="#1b1b1b"/></svg><span>(555) 210-3348</span></li>
      <li style="display:flex;gap:10px"><svg width="12" height="9" viewBox="0 0 12 9"><rect width="12" height="9" fill="#1b1b1b"/><path d="M0 0l6 5 6-5" stroke="#fff" fill="none"/></svg><span>info@viretonaviation.com</span></li>
    </ul>
  </div>
  <div class="abs" style="left:0;top:4712px;width:1200px;height:96px;background:var(--grey)"></div>
  <p class="abs" style="left:126px;top:4748px;font-size:10px">© 2026 Vireton Aviation Group. All Right Reserved</p>
  <p class="abs" style="left:884px;top:4748px;font-size:10px;word-spacing:2px;white-space:nowrap">Terms &amp; Condition &nbsp;&nbsp;&nbsp;&nbsp; Privacy Policy</p>
</footer>

</body>
</html>
```